Small Business Broker Business Card Design

A business card design for a small business brokerage, which is a financial service, not unlike real estate brokerage, but for small businesses such as laundromats, pizza shops, restaurants, cleaners etc. The designs should all be simple, more conservative in nature, using the colors and font of the logo. Again, think real estate Brokerage as a business context
Contact Information for Business Card
Name: Glen R. Harlow. Title: Small Business Advisor. Email: g.harlow@bayfieldcapitalworks.example. Mobile: (555) 274-3918. Office: (555) 806-2147. www.bayfieldcapitalworks.example

```html
<!DOCTYPE html>
<html lang="en">
<head>
<meta charset="utf-8">
<title>Bayfield Capital Works – Business Card</title>
<link rel="stylesheet" href="https://fonts.googleapis.com/css2?family=Arimo:ital,wght@0,400;0,700;1,400;1,700&family=Montserrat:wght@500;700;800&display=swap">
<style>
  :root {
    --navy: #16305f;
    --navy-deep: #0f2550;
    --navy-light: #1d3b72;
    --green: #7dc242;
    --white: #ffffff;
    --page: #1a1a1c;
  }
  * { box-sizing: border-box; margin: 0; padding: 0; }
  html, body { width: 1200px; height: 963px; overflow: hidden; }
  body {
    background: var(--page);
    display: flex;
    flex-direction: column;
    align-items: center;
    justify-content: center;
    gap: 40px;
  }
  .card {
    position: relative;
    width: 760px;
    height: 434px;
    border-radius: 22px;
    overflow: hidden;
    background: radial-gradient(ellipse at 65% 55%, var(--navy-light), var(--navy) 60%, var(--navy-deep));
    box-shadow: 0 14px 34px rgba(0,0,0,.55);
  }

  /* Front */
  .identity { position: absolute; left: 56px; top: 46px; }
  .identity__name {
    font-family: "Arimo", Arial, sans-serif;
    font-weight: 700;
    font-size: 31px;
    color: var(--green);
    text-transform: uppercase;
    letter-spacing: .5px;
  }
  .identity__title {
    font-family: "Arimo", Arial, sans-serif;
    font-style: italic;
    font-size: 19px;
    color: var(--white);
    margin-top: 4px;
  }
  .contacts {
    position: absolute; left: 56px; top: 168px;
    list-style: none;
    font-family: "Arimo", Arial, sans-serif;
    font-size: 17px;
    color: var(--white);
  }
  .contacts li { display: flex; align-items: center; gap: 10px; height: 27px; }
  .contacts svg { width: 16px; height: 16px; flex: none; }
  .brand {
    position: absolute; right: 44px; top: 176px; text-align: left;
  }
  .brand__name {
    display: flex; align-items: center; gap: 10px;
    font-family: "Montserrat", sans-serif;
    font-weight: 800;
    font-size: 18px;
    letter-spacing: 1.8px;
    color: var(--white);
    text-transform: uppercase;
  }
  .brand__mark { width: 14px; height: 14px; background: var(--green); }
  .brand__tagline {
    font-family: "Montserrat", sans-serif;
    font-weight: 600;
    font-size: 10px;
    letter-spacing: 1.6px;
    color: var(--green);
    text-transform: uppercase;
    margin-top: 4px;
    padding-left: 24px;
  }
  .swoosh { position: absolute; left: 0; bottom: 0; width: 760px; height: 434px; }

  /* Back */
  .card--back .pattern {
    position: absolute; inset: 0;
    background: linear-gradient(135deg, #1a3468, #223f7a 50%, #172f60);
  }
  .card--back .brand {
    left: 50%; top: 50%; right: auto;
    transform: translate(-50%, -50%);
  }
  .card--back .brand__name { font-size: 24px; }
  .card--back .brand__tagline { font-size: 12px; padding-left: 24px; }
</style>
</head>
<body>

  <section class="card card--front">
    <svg class="swoosh" viewBox="0 0 760 434" aria-hidden="true">
      <polygon points="0,258 0,272 450,352 760,410 760,392 460,334" fill="var(--white)"/>
      <polygon points="0,282 0,290 445,370 760,434 760,424 450,360" fill="var(--green)"/>
    </svg>

    <div class="identity">
      <h1 class="identity__name">Glen R. Harlow</h1>
      <p class="identity__title">Small Business Advisor</p>
    </div>

    <ul class="contacts">
      <li>
        <svg viewBox="0 0 16 16"><path d="M3 1.5l2.5 0 1 3.5-1.6 1.2a9 9 0 0 0 4.9 4.9L11 9.5l3.5 1v2.5c0 .8-.7 1.5-1.5 1.5A12.5 12.5 0 0 1 1.5 3c0-.8.7-1.5 1.5-1.5z" fill="var(--green)"/></svg>
        (555) 806-2147
      </li>
      <li>
        <svg viewBox="0 0 16 16"><rect x="4" y="1" width="8" height="14" rx="1.5" fill="none" stroke="var(--green)" stroke-width="1.5"/><circle cx="8" cy="12.5" r=".9" fill="var(--green)"/></svg>
        (555) 274-3918
      </li>
      <li>
        <svg viewBox="0 0 16 16"><rect x="1" y="3" width="14" height="10" fill="none" stroke="var(--green)" stroke-width="1.5"/><path d="M1 3l7 6 7-6" fill="none" stroke="var(--green)" stroke-width="1.5"/></svg>
        g.harlow@bayfieldcapitalworks.example
      </li>
      <li>
        <svg viewBox="0 0 16 16"><circle cx="8" cy="8" r="6.5" fill="none" stroke="var(--green)" stroke-width="1.4"/><ellipse cx="8" cy="8" rx="3" ry="6.5" fill="none" stroke="var(--green)" stroke-width="1.2"/><path d="M1.5 8h13M2.5 5h11M2.5 11h11" stroke="var(--green)" stroke-width="1.1"/></svg>
        www.bayfieldcapitalworks.example
      </li>
    </ul>

    <div class="brand">
      <p class="brand__name"><span class="brand__mark"></span>Bayfield Capital Works, Inc</p>
      <p class="brand__tagline">Confidently buy or sell a local business today</p>
    </div>
  </section>

  <section class="card card--back">
    <div class="pattern" role="img" aria-label="Embossed repeating brand pattern in tonal navy"></div>
    <div class="brand">
      <p class="brand__name"><span class="brand__mark"></span>Bayfield Capital Works, Inc</p>
      <p class="brand__tagline">Confidently buy or sell a local business today</p>
    </div>
  </section>

</body>
</html>
```